Wordpress Business Travel Blog and Discussion Board

Oh, Hello!

We are looking for a motivated designer to create a full, turnkey interactive WordPress website geared toward business travel that includes a news style blog (look at ByteHarbor.com and Wirevane.com for the style we like) that is seamlessly integrated with a robust message board (look at GateBanter.com and RoamLedger.com). Ok, so stick with us here because this is actually a pretty cool project that shouldn't be too hard, but yes, of course we have some curve balls that we are throwing your way. Sorry! :)

*On the front page*

- We would like to have a typical news style blog layout that is fun, somewhat professional, and easy to read. That's easy!

- Somewhere within first glance, we would like to have a short list of the most active discussions on our discussion board. (What's trending, or something like that). Not too bad, right?

- Overall, want to have a good amount of content, but we also do not want the visitor to feel as if he or she is having to sift through a lot of content to see what he or she wants to see. Great! We're past the beginning!

We will have traditional visual advertising on all of our pages. Please leave space as necessary :)

*On the Blog/News story pages*

Let's keep these simple - but there is a twist!

Let's say I create a blog/news post. I would like that blog/news post to also be opened as a discussion on the discussion board. For example, I write an article about Coastal Skyways and their service on a particular international flight. This will be opened as a discussion under the Coastal Skyways topic in the discussion board. Other users can also open new discussions under any topic on the discussion board, but they cannot post stories (unless permission is given) to the blog wall. We would like their posts to show up as regular discussion board posts while the news/blog posts by us show up as news/blog posts on the front page, *and* (oh yes we did!) as discussions in the discussion board. Of course, users will still be able to post comments to the news/blog post, which will also be posted in the discussion.

OK, does that make sense? Let me know if I can help make this more clear! :) Sorry!

*Wiki Pages*

Take a look at the Coastal Skyways example above. In that example, my news/blog entry automatically opens a new discussion post. Although we won't necessarily need to create a new wiki page, we would like to tag the post and the discussion to a wiki page about the topic. The wiki page can be created and edited by all users (and locked by us if necessary). BONUS! Can we tag more than one wiki page?

*Websites that inspire us*

ByteHarbor.com - concept and design
Wirevane.com - concept and design
GateBanter.com - concept
RoamLedger.com - concept
pomwhispers.com - concept

All of the sites above are great and we can only thrive with their great success. We are not aiming to be a competitor to the travel sites, but just another great option for interested visitors. Please do not simply copy what they have. What is posted above is a list of our favorite sites that we visit every day.

Our favorite font is Segoe UI, but please don't use this (or a similar font) too much! Maybe just titles would be great. You're the designer so you can make the call here.

Also, our favorite color is blue, but if you have another favorite color, go ahead and show us what you can do! (Don't use too much blue!)

*Oh, and One More Thing*

(I know, you thought we were done. We're not!)

Here's the killer - We would like to create a way for people to, say, enter the details of their next trip and be matched with someone who will also be on a portion of their trip.

For example, let's say I am flying Meridian Airways flight 109 from Los Angeles to New York JFK Airport this Friday. I am staying at the Bellcourt New York Times Square on Friday night, and I am flying back on Saturday night on Kestrel flight 290 from New York JFK airport back to Los Angeles. Another user will also be on the Kestrel flight back to Los Angeles with me and he entered that information in the website. (Note, the user has to manually enter this information). The other user and I will both be notified that there is at least one other user who will be on the same Kestrel flight as me. We will both have the option to reveal our online identity - which will in fact be released to each person as long as each person *mutually* agrees.

This can be very simple - almost like a dating site type of match but it is based on two people being in the same place at the same time (based on what they report). Also, we would like to be able to collect this information - not necessarily tied to the user's true identity. The information we would like to have is - what the user is claiming he or she is doing on the trip (i.e. staying at the Bellcourt Times Square, flying Meridian Airways), and whether or not the user agreed to reveal his or her identity - AND! whether or not the users both revealed their identity.

*Most Important*

HAVE FUN and THANK YOU!! :)

A couple of quick notes - this is a design and code project. We are most likely offering a more $(!) design and code project for the version 2.0 of this website once we get user feedback from this first round.

Also, the name of the website is Jaunta. (www.jaunta-example.com)

Good luck!

Reason: Extending as requested by a few designers. Only 3 more days to get your designs in!

Reason: All designs look great! Last chance for one or two more designers who have requested an extension. All designs that were already submitted on time will be considered with much higher priority. Thank you!

Requirements
Must have
• We need to have a high end, professional, modern, and clean design on the front page to entice readers to constantly visit and stay on our site.
Nice to have
• It would be great to give us the ability to automatically recognize users for visiting the website and/or participating and commenting. Social badges, recognition, etc. would be very cool.
Should not have
• Although this is a website around business travel, we do not necessarily want it to be business travel themed. There can be hints of the theme, but otherwise the visual look should be somewhat generic.

```html
<!DOCTYPE html>
<html lang="en">
<head>
<meta charset="utf-8">
<title>Saltway Travels</title>
<link href="https://fonts.googleapis.com/css2?family=Arimo:wght@400;700&family=Gelasio:ital,wght@0,400;1,400&family=Varela+Round&display=swap" rel="stylesheet">
<style>
:root{
  --orange:#f05a22;
  --orange-light:#ff8a3d;
  --red-text:#d5361a;
  --green:#8cc21c;
  --green-dark:#5f9a0a;
  --teal:#1a8fa8;
  --slate:#545c60;
  --panel:#fbf4ee;
  --text:#7a7a7a;
  --title:#4a4a4a;
  --serif:"Gelasio",Georgia,serif;
  --round:"Varela Round",sans-serif;
  --sans:"Arimo",Arial,sans-serif;
}
*{box-sizing:border-box;margin:0;padding:0}
html,body{width:1061px;height:1200px;overflow:hidden}
body{position:relative;font-family:var(--sans);background:#f1d3b6}
.scenery{position:absolute;inset:0;background:linear-gradient(180deg,#8cc3e8 0%,#c9e4f2 22%,#5fbcd6 30%,#2ba6c4 35%,#e9d1b4 42%,#f0ceae 70%,#f1d3b6 100%)}
.a{position:absolute}
.topbar{left:0;top:0;width:1061px;height:16px;background:linear-gradient(180deg,var(--orange-light),var(--orange))}
.brand{left:149px;top:34px;display:flex;align-items:center;gap:10px}
.brand-mark{width:18px;height:18px;background:var(--green)}
.brand-name{font-family:var(--round);font-size:30px;color:var(--green-dark);white-space:nowrap}
.brand-slogan{left:177px;top:78px;font-family:var(--round);font-size:14px;color:#2f6f86}
.search{left:690px;top:27px;width:220px;height:29px;background:#fff;border-radius:6px;box-shadow:0 0 3px rgba(0,0,0,.15)}
.search svg{position:absolute;right:7px;top:6px}
.nav{left:438px;top:71px;width:470px;height:33px;background:rgba(255,255,255,.65);border-radius:6px;display:flex;gap:13px;align-items:center;padding-left:13px;font-family:var(--round);font-size:14px;color:var(--red-text)}
.main{left:149px;top:142px;width:763px;height:1015px;background:var(--panel);border-radius:8px}
.welcome{left:167px;top:160px;font-family:var(--round);font-weight:400;font-size:19px;color:var(--red-text)}
.crumbs{left:167px;top:195px;font-family:var(--round);font-size:13.5px;color:var(--teal)}
.follow{left:676px;top:153px;font-family:var(--round);font-size:20px;color:var(--green)}
.social{top:153px;width:29px;height:29px;background:#fff;border:1px solid #ccc;border-radius:4px;display:flex;align-items:center;justify-content:center}
.post{left:166px;width:492px;height:239px}
.date{position:absolute;left:1px;top:0;width:37px;height:39px;background:linear-gradient(180deg,var(--orange-light),var(--orange));color:#fff;font-family:var(--serif);font-size:12.5px;text-align:center;line-height:16px;padding-top:3px}
.post-title{position:absolute;left:51px;top:-6px;font-family:var(--serif);font-weight:400;font-size:22.5px;color:var(--title);white-space:nowrap}
.meta{position:absolute;left:51px;top:28px;font-family:var(--serif);font-size:10px;color:#888;white-space:nowrap}
.meta .hl{color:var(--green-dark)}
.photo-frame{position:absolute;left:0;top:65px;width:149px;height:147px;background:#f3efea;border:1px solid #ddd;padding:8px}
.photo{width:100%;height:100%}
.excerpt{position:absolute;left:164px;top:75px;width:326px;font-size:10.3px;line-height:19.6px;color:var(--text)}
.read-more{position:absolute;left:381px;top:185px;width:100px;height:26px;background:linear-gradient(180deg,#f3703a,#dc4316);border:2px solid #fff;box-shadow:0 0 2px rgba(0,0,0,.3);color:#fff;font-weight:700;font-size:14px;padding:3px 0 0 8px}
.read-more small{font-weight:400;font-size:10px;vertical-align:4px}
.rule{position:absolute;left:0;top:226px;width:492px;height:1px;background:#e5ddd4}
.pager{left:160px;top:990px;width:498px;height:28px;background:#ece6e0;display:flex;align-items:center;font-size:10.5px;font-weight:700;color:var(--red-text)}
.pager span{width:29.4px;text-align:center}
.pager .label{width:64px;height:28px;background:var(--orange);color:#fff;line-height:28px;margin-right:3px}
.pager .cur{background:#ddd6cf;height:28px;line-height:28px}
.pager .nxt{width:21px;background:var(--orange);color:#fff;height:28px;line-height:28px;margin-left:2px}
.pager .last{width:59px;background:var(--orange);color:#fff;height:28px;line-height:28px;margin-left:2px}
.subscribe{left:663px;top:192px;width:249px;height:145px;background:linear-gradient(180deg,#2eb2d8,#4fc7e2);border-radius:6px 0 0 0}
.subscribe h2{position:absolute;left:33px;top:7px;font-family:var(--round);font-weight:400;font-size:19px;color:#fff}
.subscribe .field{position:absolute;left:13px;top:41px;width:222px;height:29px;background:#fff;border-radius:6px}
.subscribe p{position:absolute;left:20px;top:75px;width:200px;font-size:8.6px;line-height:14.5px;color:#eaf8fc;font-family:var(--round)}
.subscribe .btn{position:absolute;left:65px;top:109px;width:113px;height:24px;background:linear-gradient(180deg,#9ed52f,#6aa10e);border:1px solid #5e8d0c;border-radius:6px;color:#fff;font-family:var(--round);font-size:12.5px;text-align:center;line-height:22px}
.promo{left:663px;top:343px;width:249px;height:212px;background:#dcdcdc}
.promo-photo{position:absolute;left:9px;top:8px;width:230px;height:196px;background:linear-gradient(120deg,#2e8d7a,#d4c6a8 45%,#f2f0ea 60%,#c8442a)}
.promo-bubble{position:absolute;left:139px;top:15px;width:96px;height:60px;background:#1aa3dd;border:2px solid #fff;border-radius:8px;color:#fff;font-family:var(--round);text-align:center}
.promo-bubble b{display:block;font-weight:400;font-size:20px;margin-top:4px}
.promo-bubble span{font-size:11px}
.trending{left:663px;top:563px;width:249px;height:498px;background:linear-gradient(180deg,#555d61,#5a6266 80%,#7d8487);border-radius:6px 0 0 6px}
.trending h2{position:absolute;left:32px;top:8px;font-family:var(--round);font-weight:400;font-size:19px;color:#fff}
.trend{position:absolute;left:9px;width:236px;height:90px}
.thumb{position:absolute;left:0;top:0;width:83px;height:58px;background:#fff;padding:4px}
.thumb div{width:100%;height:100%}
.trend p{position:absolute;left:89px;top:-3px;width:145px;font-size:9.8px;line-height:14.7px;color:#fff;text-align:justify}
.trend p b{color:var(--green);margin-left:8px}
.ad{left:229px;top:1071px;width:594px;height:73px;background:#ffa800;border:1px solid #222;overflow:hidden}
.ad-photo{position:absolute;left:12px;top:0;width:70px;height:72px;background:linear-gradient(90deg,#e7a64f,#d84b7d 60%,#ffa800)}
.ad-head{position:absolute;left:89px;top:10px;font-weight:700;font-size:12.5px;line-height:11px;color:#1a1a1a}
.ad-off{position:absolute;left:238px;top:14px;font-family:var(--serif);font-weight:700;font-size:33px;color:#2a1a0a}
.ad-btn{position:absolute;left:484px;top:16px;width:95px;height:25px;background:linear-gradient(180deg,#3b8cff,#0c4fd6);border:1px solid #fff;border-radius:3px;color:#fff;font-weight:700;font-size:12px;text-align:center;line-height:23px}
.ad-url{position:absolute;left:109px;top:61px;font-size:7px;color:#fff}
.ad-by{position:absolute;right:3px;bottom:2px;font-size:9px;font-weight:700;color:#000}
.footer{left:0;top:1165px;width:1061px;height:35px;background:linear-gradient(180deg,var(--orange-light),var(--orange))}
.footer-nav{position:absolute;left:163px;top:10px;display:flex;gap:13px;font-size:11.5px;color:#fff}
.copy{position:absolute;left:814px;top:11px;font-size:10px;font-weight:700;color:#222}
</style>
</head>
<body>
<div class="scenery" role="img" aria-label="Tropical beach with palm tree, blue sea and sand behind the page"></div>
<div class="a topbar"></div>

<div class="a brand"><span class="brand-mark"></span><span class="brand-name">Saltway Travels</span></div>
<div class="a brand-slogan">Slogan goes here</div>

<div class="a search"><svg width="17" height="17" viewBox="0 0 17 17"><circle cx="6.5" cy="6.5" r="4.5" fill="none" stroke="#f05a22" stroke-width="2"/><path d="M10 10l5 5" stroke="#f05a22" stroke-width="3" stroke-linecap="round"/></svg></div>
<nav class="a nav"><span>About us</span><span>Blog</span><span>Forums</span><span>Services</span><span>Cities</span><span>Travel Guide</span><span>Contact</span></nav>

<div class="a main"></div>
<h1 class="a welcome">Welcome to Our Website</h1>
<div class="a crumbs">About Travel Stories &nbsp;&gt;&gt;&nbsp; News</div>

<div class="a follow">Follow us</div>
<div class="a social" style="left:771px"></div>
<div class="a social" style="left:805px"></div>
<div class="a social" style="left:838px"><svg width="14" height="12" viewBox="0 0 14 12"><path d="M7 12L1.2 6A3.3 3.3 0 0 1 7 2a3.3 3.3 0 0 1 5.8 4z" fill="#333"/></svg></div>
<div class="a social" style="left:872px"><svg width="13" height="13" viewBox="0 0 13 13"><circle cx="2" cy="11" r="1.7" fill="#333"/><path d="M1 6a6 6 0 0 1 6 6M1 1.5A10.5 10.5 0 0 1 11.5 12" fill="none" stroke="#333" stroke-width="2"/></svg></div>

<article class="a post" style="top:243px">
  <div class="date">Apr.<br>17</div>
  <h2 class="post-title">Top 50 mobile applications from 2010</h2>
  <div class="meta"><i>April 17th, 2011</i> &nbsp;|&nbsp; <i class="hl">12 comments</i> &nbsp;|&nbsp; posted in <span class="hl">Blog</span> &nbsp;|&nbsp; by <span class="hl">Admin</span></div>
  <div class="photo-frame"><div class="photo" role="img" aria-label="Group of travellers with luggage" style="background:linear-gradient(180deg,#f4f4f4,#d9c3a0 55%,#b83a3a)"></div></div>
  <p class="excerpt">The jukebox was softly playing the sounds of acoustic guitar. I turned it off and noticed that the simulated urban scene, just outside the window, conveyed no sound. I imagined the coffee shop as a gathering place, with ascenders of all kinds sitting at the tables discussing their next adventure...</p>
  <div class="read-more">read full <small>story</small></div>
  <div class="rule"></div>
</article>

<article class="a post" style="top:482px">
  <div class="date">Apr.<br>10</div>
  <h2 class="post-title">This is another blog entry title</h2>
  <div class="meta"><i>April 10h, 2011</i> &nbsp;|&nbsp; <i class="hl">9 comments</i> &nbsp;|&nbsp; posted in <span class="hl">Blog</span> &nbsp;|&nbsp; by <span class="hl">BlogMaster</span></div>
  <div class="photo-frame"><div class="photo" role="img" aria-label="Woman relaxing on a beach chair" style="background:linear-gradient(180deg,#4aa6df,#e8eef2 55%,#f2ede6)"></div></div>
  <p class="excerpt">There's a voice that keeps on calling me. Down the road, that's where I'll always be. Every stop I make, I make a new friend. Can't stay for long, just turn around and I'm gone again. Maybe tomorrow, I'll want to settle down, Until tomorrow, I'll just keep moving on.</p>
  <div class="read-more">read full <small>story</small></div>
  <div class="rule"></div>
</article>

<article class="a post" style="top:720px">
  <div class="date">Apr.<br>10</div>
  <h2 class="post-title">This is another blog entry title</h2>
  <div class="meta"><i>April 10h, 2011</i> &nbsp;|&nbsp; <i class="hl">9 comments</i> &nbsp;|&nbsp; posted in <span class="hl">Blog</span> &nbsp;|&nbsp; by <span class="hl">BlogMaster</span></div>
  <div class="photo-frame"><div class="photo" role="img" aria-label="Woman relaxing on a beach chair" style="background:linear-gradient(180deg,#4aa6df,#e8eef2 55%,#f2ede6)"></div></div>
  <p class="excerpt">There's a voice that keeps on calling me. Down the road, that's where I'll always be. Every stop I make, I make a new friend. Can't stay for long, just turn around and I'm gone again. Maybe tomorrow, I'll want to settle down, Until tomorrow, I'll just keep moving on.</p>
  <div class="read-more">read full <small>story</small></div>
  <div class="rule"></div>
</article>

<div class="a pager"><span class="label">Pages</span><span>1</span><span class="cur">2</span><span>3</span><span>4</span><span>5</span><span>6</span><span>7</span><span>8</span><span>9</span><span>10</span><span>11</span><span>12</span><span class="nxt">»</span><span class="last">Last page</span></div>

<section class="a subscribe">
  <svg style="position:absolute;left:9px;top:10px" width="20" height="20" viewBox="0 0 20 20"><circle cx="4" cy="16" r="3" fill="#fff"/><path d="M2 9a9 9 0 0 1 9 9M2 3a15 15 0 0 1 15 15" fill="none" stroke="#fff" stroke-width="3"/></svg>
  <h2>Subscribe News Letter</h2>
  <div class="field"></div>
  <p>Lorem Ipsum is simply dummy text of the printing and typesetting industry</p>
  <div class="btn">Subscribe Now</div>
</section>

<section class="a promo">
  <div class="promo-photo" role="img" aria-label="Summer dress and white sun hat with colourful scarf"></div>
  <div class="promo-bubble"><b>SUMMER</b><span>PERFECT ATTIRE</span></div>
</section>

<section class="a trending">
  <svg style="position:absolute;left:12px;top:9px" width="16" height="22" viewBox="0 0 16 22"><path d="M8 1a6.5 6.5 0 0 0-4 11.6V16h8v-3.4A6.5 6.5 0 0 0 8 1z" fill="none" stroke="#fff" stroke-width="1.6"/><path d="M5 18.5h6M6 21h4" stroke="#fff" stroke-width="1.6"/></svg>
  <h2>Most active Trending</h2>
  <div class="trend" style="top:42px"><div class="thumb"><div role="img" aria-label="Hammock between palm trees" style="background:linear-gradient(180deg,#2f8ad0,#9fd0ec 60%,#e9e3d6)"></div></div><p>Lorem ipsum dolor sit amet, consectetur adipisicing elit, sed do eiusmod tempor incididunt ut labore et dolore magna aliqua.<b>»</b></p></div>
  <div class="trend" style="top:132px"><div class="thumb"><div role="img" aria-label="Crowd silhouettes at sunset" style="background:linear-gradient(180deg,#fff,#f7a32a 45%,#e23b1c)"></div></div><p>Lorem ipsum dolor sit amet, consectetur adipisicing elit, sed do eiusmod tempor incididunt ut labore et dolore magna aliqua.<b>»</b></p></div>
  <div class="trend" style="top:220px"><div class="thumb"><div role="img" aria-label="Family on holiday" style="background:linear-gradient(180deg,#f5f5f5,#b8cde0 50%,#4f6f9a)"></div></div><p>Lorem ipsum dolor sit amet, consectetur adipisicing elit, sed do eiusmod tempor incididunt ut labore et dolore magna aliqua.<b>»</b></p></div>
  <div class="trend" style="top:310px"><div class="thumb"><div role="img" aria-label="Child with backpack" style="background:linear-gradient(180deg,#5fa6d8,#c8a27a 55%,#b83b36)"></div></div><p>Lorem ipsum dolor sit amet, consectetur adipisicing elit, sed do eiusmod tempor incididunt ut labore et dolore magna aliqua.<b>»</b></p></div>
  <div class="trend" style="top:403px"><div class="thumb"><div role="img" aria-label="Hammock between palm trees" style="background:linear-gradient(180deg,#2f8ad0,#9fd0ec 60%,#e9e3d6)"></div></div><p>Lorem ipsum dolor sit amet, consectetur adipisicing elit, sed do eiusmod tempor incididunt ut labore et dolore magna aliqua.<b>»</b></p></div>
</section>

<aside class="a ad">
  <div class="ad-photo" role="img" aria-label="Shopper holding gift bags"></div>
  <div class="ad-head">Find Exclusive Deals<br>Here!</div>
  <div class="ad-off">-70%</div>
  <div class="ad-btn">Learn more</div>
  <div class="ad-url">www.dealharbor-example.com</div>
  <div class="ad-by">Ads by Adnest</div>
</aside>

<footer class="a footer">
  <nav class="footer-nav"><span>Home</span><span>About us</span><span>Blog</span><span>Forums</span><span>Services</span><span>Cities</span><span>Travel Guide</span><span>Contact</span></nav>
  <div class="copy">Copyright © 2012</div>
</footer>
</body>
</html>
```